Eyecatching website design for commercial lighting business

This contest is all about the graphic design aspect. We need a striking website design for a commercial lighting company. We want something really eye catching to introduce people to our range of induction and LED lights which save businesses money on maintenance and electricity costs.

To be successful in this contest you will need to provide a design and pictures for the pages listed below.

We are using the platform velbrin.com.au and you can see the attached template which everything will be loaded into so we just need HTML files which we can upload and we can do everything else from Velbrin.

The final design should be strong and clean and use the colours and textures in the attached business card file.

Detailed requirements:

Please see attached screenshot of the website template, all we need is a fantastic graphic design and improvement/ incorporation of our logo for the following pages
Page Headings:
1. Home
About Us, Contact Us, snapshot of and link to Blog

Each of the below pages will have several paragraphs of text followed by a list of suitable products which is generated from our product catalogue.

2. Car Park Lighting
3. Educational Lighting
4. Hospitality Lighting
5. Office & Shop Lighting
6. Warehouse Lighting

Some of the website we have seen which are similar in nature are:
http://www.quorvanlamps.com.au/
http://www.tibrox.com/
http://www.gandowlumen.net/commercial-led
but we really want a modern, eye catching and memorable design

Some of the designs built on Velbrin that we like are:

http://www.pemberhollow.com.au/
http://www.marwickgoods.com.au/
http://www.kelmorabay.com.au/

I've also uploaded a couple of photos that we love. We'd like something similar for each industry.

Target Market(s)

Company Owners, Maintenance & Facilities Managers, Electrical Contractors

Industry/Entity Type

Electrical

Coding

Coded - Design and coding required

Number of Pages Required

5+ page

Font styles to use
Sans Serif

Colors
33a6d7
ec1f27

Requirements
Must have
• -Must scale to mobile
• -HTML coded files need to be provided (HTML Bootstrap)
Nice to have
• -Prefer incorporation of our logo into header bar
• -Design of 2-3 advertising banners which can be displayed on the home page
• -Prominent call to action button towards top of page 'Get a quote' or similar
• -Grid based design HTML Bootstrap

```html
<!DOCTYPE html>
<html lang="en">
<head>
<meta charset="utf-8">
<title>Harwick &amp; Doyle Business Solutions</title>
<link href="https://fonts.googleapis.com/css2?family=Open+Sans:wght@400;600;700&display=swap" rel="stylesheet">
<style>
:root{
  --red:#ec1f27;
  --blue:#33a6d7;
  --dark:#1e1e22;
  --darker:#141417;
  --header:#24252b;
  --ink:#333;
  --muted:#777;
  --white:#fff;
  --navy:#14304d;
}
*{box-sizing:border-box;margin:0;padding:0}
html,body{width:733px;height:1200px;overflow:hidden}
body{font-family:"Open Sans",Arial,sans-serif;color:var(--ink);background:var(--white);font-size:7px;line-height:1.5}
.container{width:597px;margin:0 auto;position:relative}

/* Header */
.site-header{height:60px;background:var(--header)}
.site-header .container{display:flex;justify-content:space-between;align-items:center;height:60px}
.brand{display:flex;align-items:center;gap:6px;font-weight:700;font-size:11px;color:var(--white)}
.brand-mark{width:12px;height:12px;border-radius:50%;background:var(--red)}
.main-nav{display:flex;gap:3px}
.main-nav a{display:block;padding:9px 11px;font-size:6.5px;font-weight:700;color:var(--white);background:var(--blue);text-decoration:none;text-transform:uppercase}
.main-nav a.active{background:var(--red)}

/* Hero */
.hero{height:368px;position:relative;overflow:hidden;
  background:
    linear-gradient(180deg,rgba(255,255,255,0) 0%,rgba(255,255,255,0) 62%,rgba(200,30,35,.55) 64%,rgba(160,25,30,.55) 70%,rgba(0,0,0,0) 71%),
    linear-gradient(90deg,rgba(170,200,225,.0) 0%,rgba(170,205,230,.55) 58%,rgba(150,190,220,.6) 80%,rgba(170,205,230,.0) 100%),
    linear-gradient(180deg,#f4f6f8 0%,#e3e8ec 22%,#cfd6dc 45%,#c2c9cf 62%,#9c7a5e 72%,#7e5d44 86%,#5e4432 100%)}
.hero-caption{position:absolute;left:14px;top:150px;width:190px;padding:12px 12px 11px;background:rgba(30,90,150,.85);color:var(--white)}
.hero-caption h2{font-size:10px;font-weight:700;text-transform:uppercase;margin-bottom:5px}
.hero-caption p{font-size:6px;margin-bottom:8px;color:#dbe9f5}
.btn{display:inline-block;background:var(--red);color:var(--white);font-size:6px;font-weight:700;padding:5px 10px;text-transform:uppercase;text-decoration:none}
.hero-arrow{position:absolute;top:162px;width:20px;height:20px}
.hero-arrow.prev{left:8px}.hero-arrow.next{right:8px}

/* Welcome */
.welcome{height:172px;padding-top:22px}
.welcome .container{display:flex;justify-content:space-between}
.welcome-text{width:360px}
.section-title{font-size:10px;font-weight:700;text-transform:uppercase;color:var(--dark);margin-bottom:8px}
.welcome-text p{color:var(--muted);font-size:6.5px;margin-bottom:7px}
.welcome-media{width:225px;height:118px;position:relative;
  background:linear-gradient(180deg,#e8edf1 0%,#c9d4dc 40%,#8d9aa5 62%,#8a6a50 78%,#5a4030 100%)}
.welcome-media svg{position:absolute;left:100px;top:46px}

/* Products */
.products{background:var(--blue);height:245px;padding-top:20px}
.products h2{text-align:center;color:var(--white);font-size:10px;font-weight:700;margin-bottom:12px}
.product-grid{display:flex;justify-content:space-between}
.product-card{width:140px;background:var(--white);text-align:center;padding:5px 5px 0}
.product-image{height:80px;margin-bottom:6px}
.product-image.car{background:linear-gradient(180deg,#0f2a55 0%,#2f5f9c 45%,#8fb4d8 62%,#4b5c70 75%,#2a3440 100%)}
.product-image.edu{background:radial-gradient(circle at 50% 40%,#f7f3e4 0%,#dfe6e8 35%,#8eb7c4 70%,#5d8797 100%)}
.product-image.hos{background:linear-gradient(180deg,#2a2220 0%,#6b4a2e 40%,#c98c45 65%,#e9b56a 80%,#7a5030 100%)}
.product-image.off{background:linear-gradient(180deg,#f2f4f6 0%,#dde3e8 40%,#b8c3cc 70%,#8e9aa4 100%)}
.product-card h3{font-size:7.5px;font-weight:600;color:var(--dark);margin-bottom:3px}
.product-card p{font-size:5.5px;color:var(--muted);padding:0 6px;margin-bottom:8px}
.product-card .btn{display:block;margin:0 -5px}

/* Blog */
.blog{height:163px;padding-top:18px}
.blog h2{text-align:center;font-size:10px;font-weight:700;color:var(--dark);margin-bottom:16px}
.blog-grid{display:flex;justify-content:space-between}
.blog-post{width:195px;display:flex;gap:8px;border-left:1px solid #eee}
.blog-post:first-child{border-left:0}
.post-date{color:var(--red);font-weight:700;text-align:center;width:22px;flex-shrink:0;padding-left:4px}
.post-date span{display:block;font-size:6px}
.post-date strong{display:block;font-size:11px;line-height:1.1}
.blog-post h3{font-size:6.5px;font-weight:600;color:var(--dark);margin-bottom:4px}
.blog-post p{font-size:5.5px;color:var(--muted)}

/* Footer */
.site-footer{background:var(--dark);color:#bbb;height:167px;padding-top:18px}
.footer-grid{display:flex;justify-content:space-between}
.footer-col h4{color:var(--white);font-size:7.5px;font-weight:700;text-transform:uppercase;margin-bottom:9px}
.footer-col ul{list-style:none}
.footer-col li{font-size:5.5px;margin-bottom:7px;padding-left:7px;position:relative}
.footer-col li::before{content:"";position:absolute;left:0;top:2px;width:3px;height:3px;background:var(--red)}
.link-cols{display:flex;gap:26px}
.contact-col{width:110px}
.contact-btn{display:block;background:var(--blue);color:var(--white);font-size:5.5px;font-weight:600;padding:5px 7px;margin-bottom:4px}
.social{display:flex;gap:3px;margin-top:5px}
.social span{width:11px;height:11px;background:var(--red);display:block}
.copyright{background:var(--darker);color:#888;font-size:5.5px;height:25px;line-height:25px}
</style>
</head>
<body>
<header class="site-header">
  <div class="container">
    <div class="brand"><span class="brand-mark"></span>Harwick &amp; Doyle</div>
    <nav class="main-nav">
      <a class="active" href="#">Home</a>
      <a href="#">About Us</a>
      <a href="#">Products</a>
      <a href="#">Blog</a>
      <a href="#">Contact Us</a>
    </nav>
  </div>
</header>

<section class="hero" role="img" aria-label="Bright modern conference room lit by ceiling panel lights, red chairs around a long table">
  <div class="container" style="height:368px">
    <div class="hero-caption">
      <h2>Save your electricity costs</h2>
      <p>Lower energy bills with smart induction and LED fittings built for modern commercial spaces.</p>
      <a class="btn" href="#">Learn more</a>
    </div>
  </div>
  <svg class="hero-arrow prev" viewBox="0 0 20 20"><rect width="20" height="20" fill="#fff" opacity=".85"/><path d="M12 5 7 10l5 5" fill="none" stroke="#333" stroke-width="2"/></svg>
  <svg class="hero-arrow next" viewBox="0 0 20 20"><rect width="20" height="20" fill="#fff" opacity=".85"/><path d="M8 5l5 5-5 5" fill="none" stroke="#333" stroke-width="2"/></svg>
</section>

<section class="welcome">
  <div class="container">
    <div class="welcome-text">
      <h2 class="section-title">Welcome to Harwick &amp; Doyle Business Solutions</h2>
      <p>Retrofitting your lighting is a commercial decision that pays back through lower power bills and far fewer maintenance callouts across every site you manage.</p>
      <p>We supply induction and LED fittings for car parks, schools, venues and offices, backed by local advice and fast delivery.</p>
      <a class="btn" href="#">Read more</a>
    </div>
    <div class="welcome-media" role="img" aria-label="Video still of a lit meeting room">
      <svg width="26" height="26" viewBox="0 0 26 26"><circle cx="13" cy="13" r="13" fill="#fff" opacity=".9"/><path d="M10 8l8 5-8 5z" fill="#333"/></svg>
    </div>
  </div>
</section>

<section class="products">
  <div class="container">
    <h2>OUR PRODUCTS</h2>
    <div class="product-grid">
      <article class="product-card">
        <div class="product-image car" role="img" aria-label="Car park lit by induction lights at night"></div>
        <h3>Car Park Lighting</h3>
        <p>Durable fittings that cut running costs and brighten every space.</p>
        <a class="btn" href="#">Read more</a>
      </article>
      <article class="product-card">
        <div class="product-image edu" role="img" aria-label="Classroom ceiling lighting"></div>
        <h3>Educational Lighting</h3>
        <p>Durable fittings that cut running costs and brighten every space.</p>
        <a class="btn" href="#">Read more</a>
      </article>
      <article class="product-card">
        <div class="product-image hos" role="img" aria-label="Warm lit hospitality venue"></div>
        <h3>Hospitality Lighting</h3>
        <p>Durable fittings that cut running costs and brighten every space.</p>
        <a class="btn" href="#">Read more</a>
      </article>
      <article class="product-card">
        <div class="product-image off" role="img" aria-label="Open plan office with panel lights"></div>
        <h3>Office Lighting</h3>
        <p>Durable fittings that cut running costs and brighten every space.</p>
        <a class="btn" href="#">Read more</a>
      </article>
    </div>
  </div>
</section>

<section class="blog">
  <div class="container">
    <h2>OUR BLOG</h2>
    <div class="blog-grid">
      <article class="blog-post">
        <div class="post-date"><span>MAR</span><strong>26</strong></div>
        <div><h3>Why induction lighting suits busy car parks and loading docks</h3><p>Short notes on energy savings, maintenance and payback for facility managers.</p></div>
      </article>
      <article class="blog-post">
        <div class="post-date"><span>MAR</span><strong>26</strong></div>
        <div><h3>How LED upgrades lower costs for schools and campuses</h3><p>Short notes on energy savings, maintenance and payback for facility managers.</p></div>
      </article>
      <article class="blog-post">
        <div class="post-date"><span>MAR</span><strong>27</strong></div>
        <div><h3>Simple steps to plan an office lighting retrofit</h3><p>Short notes on energy savings, maintenance and payback for facility managers.</p></div>
      </article>
    </div>
  </div>
</section>

<footer>
  <div class="site-footer">
    <div class="container footer-grid">
      <div class="footer-col"><h4>Quick Links</h4><ul><li>Our company</li><li>News</li><li>Blog</li><li>Downloads</li></ul></div>
      <div class="footer-col"><h4>Information</h4><ul><li>Home</li><li>About Us</li><li>Products</li><li>Contact Us</li></ul></div>
      <div class="footer-col"><h4>Company</h4>
        <div class="link-cols">
          <ul><li>Car Park Lighting</li><li>Educational Lighting</li><li>Hospitality Lighting</li><li>Office Lighting</li></ul>
          <ul><li>Warehouse Lighting</li><li>Privacy Policy</li><li>Sitemap</li></ul>
        </div>
      </div>
      <div class="footer-col contact-col"><h4>Contact Us</h4>
        <span class="contact-btn">GET A QUOTE</span>
        <span class="contact-btn">CALL 1300 000 000</span>
        <span class="contact-btn">EMAIL US</span>
        <div class="social"><span></span><span></span><span></span><span></span></div>
      </div>
    </div>
  </div>
  <div class="copyright"><div class="container">Copyright © 2015 Harwick &amp; Doyle Business Solutions. All rights reserved.</div></div>
</footer>
</body>
</html>
```